Irrigation Business needs their business cards modernised and revamped

I would like to keep my current logo, colours and revamp the format of the card.

I would like the card to be clean yet important.

Im not sure if you include texture but i would like the named logo to be indented into the card etc.

show me something alive and free something thats clinical to the point yet has a feel of achievement. i would like people to go nice card.

Target Market(s)

high end clients, corporate, sports field manger, the guys that make the decisions

Industry/Entity Type

Business

Contact Information for Business Card

nformation to be included

Dean Harlow (Director)
0487305526
dean@kolvat.biz
www.kestonfieldworks.com

instagram logo
google logo
facebook logo

Colors

Designer to choose colors to be used in the design.

Requirements
Nice to have
• indentations a really nice feel to the card good texture

```html
<!DOCTYPE html>
<html lang="en">
<head>
<meta charset="utf-8">
<title>Keston Fieldworks – Business Card</title>
<link rel="stylesheet" href="https://fonts.googleapis.com/css2?family=Open+Sans:wght@400;600&display=swap">
<style>
  :root {
    --stage: #d9d6d2;
    --card: #121314;
    --card-edge: #1d1f21;
    --brand-blue: #2f8fd0;
    --brand-green: #3fae5a;
    --ink: #f2f2f2;
    --gloss: #6b6e72;
    --gloss-light: #9a9da1;
  }
  * { box-sizing: border-box; margin: 0; padding: 0; }
  html, body {
    width: 1200px; height: 864px; overflow: hidden;
    background: var(--stage);
    font-family: "Open Sans", Arial, sans-serif;
  }
  .stage { position: relative; width: 1200px; height: 864px; }

  .card {
    position: absolute;
    width: 560px; height: 320px;
    background: var(--card);
    border-radius: 6px;
    box-shadow: 0 10px 28px rgba(0,0,0,.28);
    overflow: hidden;
  }

  /* Back of card */
  .card--back { left: 70px; top: 90px; }
  .back-mark {
    position: absolute; left: 0; right: 0; top: 96px;
    display: flex; flex-direction: column; align-items: center; gap: 14px;
  }
  .back-mark__disc {
    width: 64px; height: 64px; border-radius: 50%;
    background: radial-gradient(circle at 35% 30%, var(--gloss-light), var(--gloss) 60%, #3d3f42);
  }
  .back-mark__name {
    font-weight: 600; font-size: 24px; letter-spacing: 3px;
    color: var(--gloss); text-transform: uppercase;
  }
  .social-row {
    position: absolute; left: 0; right: 0; top: 236px;
    display: flex; justify-content: center; gap: 8px;
  }
  .social-row__dot {
    width: 18px; height: 18px; border-radius: 50%;
    background: var(--gloss);
  }

  /* Front of card */
  .card--front { left: 570px; top: 454px; }
  .brand {
    position: absolute; left: 0; top: 0; width: 300px; height: 320px;
    display: flex; flex-direction: column; align-items: center; justify-content: center; gap: 12px;
  }
  .brand__disc {
    width: 50px; height: 50px; border-radius: 50%;
    background: var(--brand-blue);
  }
  .brand__name {
    font-weight: 600; font-size: 21px; letter-spacing: 1px;
    color: var(--brand-blue); text-transform: uppercase;
  }
  .divider {
    position: absolute; left: 300px; top: 80px; width: 2px; height: 160px;
    background: linear-gradient(to bottom, transparent, #8a8d90 50%, transparent);
  }
  .contact {
    position: absolute; left: 328px; top: 100px; width: 220px;
  }
  .contact__name {
    font-weight: 600; font-size: 15px; color: var(--brand-blue);
    text-transform: uppercase; line-height: 1.15;
  }
  .contact__role {
    font-weight: 400; font-size: 15px; color: var(--brand-green);
    text-transform: uppercase; line-height: 1.15; margin-bottom: 14px;
  }
  .contact__line {
    display: flex; align-items: center; gap: 8px;
    font-size: 13.5px; color: var(--ink); line-height: 1.55;
    white-space: nowrap;
  }
  .contact__icon { width: 11px; height: 11px; flex: none; fill: var(--ink); }
</style>
</head>
<body>
<main class="stage">

  <section class="card card--back" aria-label="Card back">
    <div class="back-mark">
      <span class="back-mark__disc"></span>
      <span class="back-mark__name">Keston Fieldworks</span>
    </div>
    <div class="social-row" aria-label="Social media links">
      <span class="social-row__dot"></span>
      <span class="social-row__dot"></span>
      <span class="social-row__dot"></span>
    </div>
  </section>

  <section class="card card--front" aria-label="Card front">
    <div class="brand">
      <span class="brand__disc"></span>
      <span class="brand__name">Keston Fieldworks</span>
    </div>
    <span class="divider"></span>
    <div class="contact">
      <p class="contact__name">Dean Harlow</p>
      <p class="contact__role">Director</p>
      <p class="contact__line">
        <svg class="contact__icon" viewBox="0 0 12 12" aria-hidden="true">
          <path d="M1 4 Q6 0 11 4 L9.5 5.5 L8 4.5 L8 3.5 Q6 3 4 3.5 L4 4.5 L2.5 5.5 Z"/>
          <rect x="2.5" y="6" width="7" height="5" rx="1"/>
        </svg>0487305526
      </p>
      <p class="contact__line">
        <svg class="contact__icon" viewBox="0 0 12 12" aria-hidden="true">
          <path d="M0.5 2.5 H11.5 V9.5 H0.5 Z M1 3 L6 6.8 L11 3" stroke="#121314" stroke-width="0.8"/>
        </svg>dean@kolvat.biz
      </p>
      <p class="contact__line">
        <svg class="contact__icon" viewBox="0 0 12 12" aria-hidden="true">
          <circle cx="6" cy="6" r="5.5"/>
          <path d="M0.5 6 H11.5 M6 0.5 V11.5 M6 0.5 Q2.5 6 6 11.5 M6 0.5 Q9.5 6 6 11.5" stroke="#121314" stroke-width="0.7" fill="none"/>
        </svg>www.kestonfieldworks.com
      </p>
    </div>
  </section>

</main>
</body>
</html>
```